A Modern & Sleek "Coming Soon" Page for an A.I Recruiting App

For the “Coming Soon” website, a simple background with no people in it. I've attached an A.I image of what the page should generally look like.

- A single mobile phone as the main focus where the user actually clicks on the, “notify me” button (after entering their email address).
- In the background where the pillars/columns are seen in the example, should be subtle pad locks that are in their opened position with a key inside the lock. I've attached images to try to illustrate this idea, but they are far away in style from what I'm looking for.

SLOGAN: Unlocking the power of meaningful connections
LOGO/TITLE: Should be the name as shown in image with only the name "KelvoLink" on it
COLORS: Purplish/blue hues. Should not be too feminine
NOTE: The user should only click once when signing up/entering their email.

Product: A recruiting platform that matches employers/employees with A.I. and prioritizing cultural fit/values system before skills. The industry we are tackling first is the caregiving industry (nannies, tutors, elderly). All users will be background screened and that info lives on the blockchain. All users will have the option to review and be reviewed/rated.

```html
<!DOCTYPE html>
<html lang="en">
<head>
<meta charset="UTF-8">
<title>KelvoLink – Coming Soon</title>
<link href="https://fonts.googleapis.com/css2?family=Poppins:wght@300;400;500;600&display=swap" rel="stylesheet">
<style>
  :root {
    --brand: #9a2a95;
    --ink: #1a1a1a;
    --muted: #5a5a5a;
    --white: #ffffff;
    --hero-navy: #2c2e6e;
    --hero-indigo: #4a4596;
    --hero-violet: #7d5aae;
    --hero-lilac: #a983c4;
    --screen-top: #4f3580;
    --screen-bottom: #2f1f5a;
  }
  * { box-sizing: border-box; margin: 0; padding: 0; }
  html, body { width: 929px; height: 1200px; overflow: hidden; background: var(--white); }
  body { font-family: "Poppins", sans-serif; color: var(--ink); position: relative; }

  .site-header { position: absolute; top: 0; left: 0; width: 929px; height: 80px; background: var(--white); }
  .wordmark { position: absolute; left: 86px; top: 20px; font-weight: 300; font-size: 29px; letter-spacing: 2px; color: var(--brand); text-transform: uppercase; line-height: 40px; }
  .menu-toggle { position: absolute; left: 800px; top: 26px; width: 40px; height: 28px; }
  .menu-toggle span { position: absolute; left: 0; height: 2.5px; background: var(--brand); border-radius: 2px; }
  .menu-toggle span:nth-child(1) { top: 0; width: 40px; }
  .menu-toggle span:nth-child(2) { top: 12.5px; width: 30px; left: 10px; }
  .menu-toggle span:nth-child(3) { top: 25px; width: 40px; }

  .hero { position: absolute; top: 80px; left: 0; width: 929px; height: 464px;
    background: radial-gradient(ellipse 55% 70% at 55% 15%, var(--hero-lilac) 0%, rgba(125,90,174,0.85) 45%, transparent 100%),
                linear-gradient(100deg, var(--hero-navy) 0%, var(--hero-indigo) 28%, var(--hero-violet) 55%, #6b4f9e 80%, var(--hero-navy) 100%); }
  .hero-title { position: absolute; left: 320px; top: 144px; font-weight: 500; font-size: 32px; line-height: 41px; color: var(--white); }
  .btn { position: absolute; display: flex; align-items: center; justify-content: center; background: var(--brand); color: var(--white); font-weight: 500; font-size: 12.5px; border-radius: 7px; text-decoration: none; }
  .btn-signup { left: 322px; top: 249px; width: 129px; height: 37px; }
  .lock-art { position: absolute; left: 630px; top: 150px; width: 240px; height: 252px; border-radius: 40%;
    background: radial-gradient(ellipse at 50% 55%, rgba(30,45,100,0.75) 0%, rgba(50,80,140,0.45) 45%, transparent 72%); }

  .phone { position: absolute; left: 65px; top: 149px; width: 212px; height: 433px; border-radius: 30px; background: #111; padding: 8px; box-shadow: 0 14px 24px rgba(0,0,0,0.12); }
  .phone-screen { width: 100%; height: 100%; border-radius: 23px; background: linear-gradient(180deg, var(--screen-top) 0%, var(--screen-bottom) 60%, #3d2a6c 100%); position: relative; text-align: center; color: var(--white); }
  .phone-notch { position: absolute; left: 45px; top: 0; width: 106px; height: 14px; background: #111; border-radius: 0 0 10px 10px; }
  .phone-brand { position: absolute; top: 103px; width: 100%; font-weight: 300; font-size: 20px; letter-spacing: 1px; text-transform: uppercase; line-height: 28px; }
  .phone-tagline { position: absolute; top: 143px; width: 100%; font-size: 12px; line-height: 18px; }
  .phone-email { position: absolute; left: 24px; top: 250px; width: 148px; height: 29px; border-radius: 15px; background: rgba(255,255,255,0.12); border: 1px solid rgba(255,255,255,0.45); display: flex; align-items: center; padding-left: 12px; font-size: 10.5px; color: rgba(255,255,255,0.75); }
  .phone-notify { position: absolute; left: 38px; top: 294px; width: 120px; height: 29px; border: 1px solid rgba(255,255,255,0.85); border-radius: 15px; display: flex; align-items: center; justify-content: center; font-weight: 600; font-size: 12px; }
  .phone-footnote { position: absolute; top: 339px; width: 100%; font-size: 12px; line-height: 18px; }

  .about { position: absolute; top: 640px; left: 0; width: 929px; text-align: center; }
  .about-title { font-weight: 600; font-size: 30px; color: var(--brand); line-height: 46px; }
  .about-lead { margin-top: 4px; font-size: 11.3px; color: var(--ink); }
  .about-body { width: 700px; margin: 22px auto 0; font-weight: 300; font-size: 11.3px; line-height: 20px; color: var(--muted); }
  .btn-learn { left: 400px; top: 868px; width: 129px; height: 37px; }

  .footer-wave { position: absolute; left: 0; top: 910px; width: 929px; height: 290px; }
  .footer-brand { position: absolute; top: 1048px; width: 929px; text-align: center; font-weight: 300; font-size: 32px; letter-spacing: 3px; color: var(--white); text-transform: uppercase; line-height: 42px; }
  .social-list { position: absolute; top: 1104px; left: 0; width: 929px; display: flex; justify-content: center; gap: 3px; list-style: none; }
  .social-list li { width: 21px; height: 21px; border: 1.3px solid var(--white); border-radius: 50%; }
  .footer-rule { position: absolute; left: 86px; top: 1160px; width: 757px; height: 1px; background: rgba(255,255,255,0.55); }
  .copyright { position: absolute; top: 1169px; width: 929px; text-align: center; font-size: 11px; color: var(--white); }
</style>
</head>
<body>
  <header class="site-header">
    <div class="wordmark">KelvoLink</div>
    <div class="menu-toggle" aria-label="Menu"><span></span><span></span><span></span></div>
  </header>

  <section class="hero">
    <div class="lock-art" role="img" aria-label="Open padlock with a key inserted"></div>
    <h1 class="hero-title">Unlocking the power of<br>meaningful connections</h1>
    <a class="btn btn-signup">Sign Up</a>
  </section>

  <div class="phone">
    <div class="phone-screen">
      <div class="phone-notch"></div>
      <div class="phone-brand">KelvoLink</div>
      <p class="phone-tagline">Unlocking power of<br>meaningful connections</p>
      <div class="phone-email">Enter your email</div>
      <div class="phone-notify">Notify Me</div>
      <p class="phone-footnote">Coming soon for<br>caregivers, families</p>
    </div>
  </div>

  <section class="about">
    <h2 class="about-title">About Us</h2>
    <p class="about-lead">Lorem ipsum dolor sit amet, consectetur adipiscing elit, sed do eiusmod</p>
    <p class="about-body">Sed ut perspiciatis unde omnis iste natus error sit voluptatem accusantium doloremque laudantium, totam rem aperiam, eaque ipsa quae ab illo inventore veritatis et quasi architecto beatae vitae dicta sunt explicabo. Nemo enim ipsam voluptatem quia voluptas sit aspernatur aut odit aut fugit, sed quia consequuntur magni dolores eos qui ratione voluptatem sequi nesciunt. Neque porro quisquam est, qui dolorem ipsum quia dolor sit amet, consectetur, adipisci velit, sed quia non numquam eius modi tempora incidunt ut labore et dolore magnam aliquam quaerat voluptatem. Ut enim ad minima veniam, quis nostrum exercitationem ullam</p>
  </section>
  <a class="btn btn-learn">Learn More</a>

  <footer>
    <svg class="footer-wave" viewBox="0 0 929 290" width="929" height="290" aria-hidden="true">
      <path d="M0 6 Q464.5 82 929 6 L929 290 L0 290 Z" fill="var(--brand)"/>
      <path d="M0 17 Q464.5 92 929 17" fill="none" stroke="var(--white)" stroke-width="4"/>
    </svg>
    <div class="footer-brand">KelvoLink</div>
    <ul class="social-list" aria-label="Social links">
      <li></li><li></li><li></li><li></li><li></li>
    </ul>
    <div class="footer-rule"></div>
    <p class="copyright">© 2024 KelvoLink. All Rights Reserved.</p>
  </footer>
</body>
</html>
```